I would like to modify/update my 2 step login screen

I want a more modern looking login page for our document imaging application. I need to keep all of the same elements and buttons that currently exist. The first 2 screens are the login. The 3rd is a screenshot of the actual application home page.

```html
<!DOCTYPE html>
<html lang="en">
<head>
<meta charset="utf-8">
<title>MRDS Login Flow</title>
<link rel="stylesheet" href="https://fonts.googleapis.com/css2?family=Inter:wght@400;500;600;700&display=swap">
<style>
:root{
  --page:#f0f0f0;
  --brand-pane:#3b3c3e;
  --white:#ffffff;
  --ink:#333538;
  --muted:#8a8d91;
  --line:#dcdee0;
  --bar:#f5f5f5;
  --green:#4caf50;
  --disabled:#c9cacc;
  --error:#e06262;
}
*{margin:0;padding:0;box-sizing:border-box}
html,body{width:1200px;height:482px;overflow:hidden;background:var(--page);font-family:"Inter",sans-serif}
.stage{position:absolute;left:0;top:0;width:2576px;height:1036px;transform:scale(0.46584);transform-origin:0 0}
.screen{position:absolute;width:796px;height:447px;background:var(--white);overflow:hidden}
.brand-pane{position:absolute;left:0;top:0;width:348px;height:447px;background:var(--brand-pane);color:var(--white)}
.brand-name{position:absolute;left:0;right:0;top:170px;display:flex;align-items:center;justify-content:center;gap:8px;font-size:15px;font-weight:700;letter-spacing:.5px}
.brand-mark{width:22px;height:22px;border-radius:50%;background:var(--white)}
.brand-links{position:absolute;left:0;right:0;top:399px;text-align:center;font-size:6.5px;font-weight:500}
.brand-links .dot{margin:0 5px}
.copyright{position:absolute;left:0;right:0;top:415px;text-align:center;font-size:6.5px;color:#9a9b9e}
.form-pane{position:absolute;left:348px;top:0;width:448px;height:447px}
.alert{position:absolute;left:0;top:0;width:448px;height:23px;background:var(--error);color:var(--white);font-size:7px;display:flex;align-items:center;justify-content:center}
.title{position:absolute;left:107px;top:56px;font-size:14px;font-weight:600;color:var(--ink)}
.field{position:absolute;left:107px;width:233px;height:25px;border:1px solid var(--line);border-radius:2px;display:flex;align-items:center;padding:0 8px;font-size:7.5px;color:var(--ink)}
.field.is-focus{border-color:var(--green)}
.field.is-error{border-color:var(--error)}
.field svg{width:10px;height:10px;flex:none}
.field .value{margin-left:8px;flex:1}
.field .placeholder{color:var(--muted)}
.field .dots{letter-spacing:1px;font-size:9px}
.field .tool{margin-left:6px;color:#9a9c9f}
.field .sep{width:1px;height:11px;background:var(--line);margin-left:6px}
.btn{position:absolute;height:23px;border-radius:2px;font-size:7.5px;font-weight:600;color:var(--white);display:flex;align-items:center;justify-content:center;background:var(--green)}
.btn.is-disabled{background:var(--disabled)}
.db-row{position:absolute;left:107px;top:97px;display:flex;align-items:center;font-size:7.5px;color:#555}
.db-row .back{width:10px;height:10px}
.db-row .divider{width:1px;height:12px;background:var(--line);margin:0 12px 0 9px}
.db-row .db-icon{width:10px;height:10px;margin-right:7px}
.forgot{position:absolute;left:107px;top:219px;font-size:7.5px;font-weight:500;color:var(--green)}
.or-rule{position:absolute;left:107px;top:253px;width:233px;height:1px;background:var(--line)}
.or-rule span{position:absolute;left:50%;top:-4px;transform:translateX(-50%);background:var(--white);padding:0 6px;font-size:6px;color:var(--muted)}
.sso{position:absolute;top:272px;width:73px;height:57px;border:1px solid var(--line);border-radius:2px;text-align:center;font-size:6.5px;line-height:10px;color:#555}
.sso .mark{width:10px;height:10px;border-radius:50%;background:#6d7074;margin:10px auto 6px}
.notice{position:absolute;left:0;bottom:0;width:448px;height:22px;background:var(--bar);border-top:1px solid #e6e6e6;font-size:6.5px;color:#555;display:flex;align-items:center;justify-content:center}
.notice b{font-weight:600;color:var(--ink)}
</style>
</head>
<body>
<svg width="0" height="0" style="position:absolute">
  <defs>
    <symbol id="i-db" viewBox="0 0 12 12"><rect x="1" y="1.5" width="10" height="4" rx="1" fill="none" stroke="currentColor" stroke-width="1.1"/><rect x="1" y="6.5" width="10" height="4" rx="1" fill="none" stroke="currentColor" stroke-width="1.1"/></symbol>
    <symbol id="i-user" viewBox="0 0 12 12"><circle cx="6" cy="4" r="2.4" fill="none" stroke="currentColor" stroke-width="1.1"/><path d="M1.5 11c.5-2.6 2.3-3.8 4.5-3.8S10 8.4 10.5 11" fill="none" stroke="currentColor" stroke-width="1.1"/></symbol>
    <symbol id="i-lock" viewBox="0 0 12 12"><rect x="2" y="5" width="8" height="6" rx="1" fill="none" stroke="currentColor" stroke-width="1.1"/><path d="M4 5V3.5a2 2 0 0 1 4 0V5" fill="none" stroke="currentColor" stroke-width="1.1"/></symbol>
    <symbol id="i-clear" viewBox="0 0 12 12"><circle cx="6" cy="6" r="4.6" fill="none" stroke="currentColor" stroke-width="1"/><path d="M4.2 4.2l3.6 3.6M7.8 4.2L4.2 7.8" stroke="currentColor" stroke-width="1"/></symbol>
    <symbol id="i-eye" viewBox="0 0 12 12"><path d="M1 6s2-3.5 5-3.5S11 6 11 6 9 9.5 6 9.5 1 6 1 6z" fill="none" stroke="currentColor" stroke-width="1"/><circle cx="6" cy="6" r="1.5" fill="none" stroke="currentColor" stroke-width="1"/><path d="M2 10L10 2" stroke="currentColor" stroke-width="1"/></symbol>
    <symbol id="i-back" viewBox="0 0 12 12"><path d="M11 6H1.5M5 2.5L1.5 6 5 9.5" fill="none" stroke="currentColor" stroke-width="1"/></symbol>
  </defs>
</svg>

<main class="stage">

  <!-- Step 1: empty -->
  <section class="screen" style="left:47px;top:47px">
    <div class="brand-pane">
      <div class="brand-name"><span class="brand-mark"></span>MERIDIAN SYSTEMS</div>
      <p class="brand-links">Privacy<span class="dot">•</span>Remote Support<span class="dot">•</span>Contact Us</p>
      <p class="copyright">Copyright 2007-2024 Meridian Systems</p>
    </div>
    <div class="form-pane">
      <h1 class="title">Login to MRDS</h1>
      <div class="field" style="top:101px"><svg style="color:#666"><use href="#i-db"/></svg><span class="value placeholder">Database</span></div>
      <div class="btn is-disabled" style="left:290px;top:145px;width:50px">NEXT</div>
      <p class="notice">All activity on this site is being recorded. Your IP Address is being saved as '<b>192.168.168.134</b>'.</p>
    </div>
  </section>

  <!-- Step 1: filled -->
  <section class="screen" style="left:890px;top:47px">
    <div class="brand-pane">
      <div class="brand-name"><span class="brand-mark"></span>MERIDIAN SYSTEMS</div>
      <p class="brand-links">Privacy<span class="dot">•</span>Remote Support<span class="dot">•</span>Contact Us</p>
      <p class="copyright">Copyright 2007-2024 Meridian Systems</p>
    </div>
    <div class="form-pane">
      <h1 class="title">Login to MRDS</h1>
      <div class="field is-focus" style="top:101px"><svg style="color:#666"><use href="#i-db"/></svg><span class="value">ABC12345|</span><svg class="tool"><use href="#i-clear"/></svg></div>
      <div class="btn" style="left:290px;top:145px;width:50px">NEXT</div>
      <p class="notice">All activity on this site is being recorded. Your IP Address is being saved as '<b>192.168.168.134</b>'.</p>
    </div>
  </section>

  <!-- Step 1: error -->
  <section class="screen" style="left:1733px;top:47px">
    <div class="brand-pane">
      <div class="brand-name"><span class="brand-mark"></span>MERIDIAN SYSTEMS</div>
      <p class="brand-links">Privacy<span class="dot">•</span>Remote Support<span class="dot">•</span>Contact Us</p>
      <p class="copyright">Copyright 2007-2024 Meridian Systems</p>
    </div>
    <div class="form-pane">
      <div class="alert">Invalid database. Please enter the correct data and try again.</div>
      <h1 class="title">Login to MRDS</h1>
      <div class="field is-error" style="top:101px"><svg style="color:#666"><use href="#i-db"/></svg><span class="value">ABC12345XYZ</span><svg class="tool"><use href="#i-clear"/></svg></div>
      <div class="btn" style="left:290px;top:145px;width:50px">NEXT</div>
      <p class="notice">All activity on this site is being recorded. Your IP Address is being saved as '<b>192.168.168.134</b>'.</p>
    </div>
  </section>

  <!-- Step 2: empty -->
  <section class="screen" style="left:47px;top:541px">
    <div class="brand-pane">
      <div class="brand-name"><span class="brand-mark"></span>MERIDIAN SYSTEMS</div>
      <p class="brand-links">Privacy<span class="dot">•</span>Remote Support<span class="dot">•</span>Contact Us</p>
      <p class="copyright">Copyright 2007-2024 Meridian Systems</p>
    </div>
    <div class="form-pane">
      <h1 class="title">Login to MRDS</h1>
      <div class="db-row"><svg class="back" style="color:#888"><use href="#i-back"/></svg><span class="divider"></span><svg class="db-icon"><use href="#i-db"/></svg>Database : ABC12345</div>
      <div class="field" style="top:135px"><svg style="color:#666"><use href="#i-user"/></svg><span class="value placeholder">Username</span></div>
      <div class="field" style="top:167px"><svg style="color:#666"><use href="#i-lock"/></svg><span class="value placeholder">Password</span><svg class="tool"><use href="#i-eye"/></svg></div>
      <a class="forgot">Forgot Password?</a>
      <div class="btn is-disabled" style="left:287px;top:211px;width:53px">LOGIN</div>
      <div class="or-rule"><span>OR</span></div>
      <div class="sso" style="left:107px"><div class="mark"></div>Login with<br>Keyway</div>
      <div class="sso" style="left:187px"><div class="mark"></div>Login with<br>Northgate</div>
      <div class="sso" style="left:267px"><div class="mark"></div>Login with<br>SinglePass</div>
      <p class="notice">All activity on this site is being recorded. Your IP Address is being saved as '<b>192.168.168.134</b>'.</p>
    </div>
  </section>

  <!-- Step 2: filled -->
  <section class="screen" style="left:890px;top:541px">
    <div class="brand-pane">
      <div class="brand-name"><span class="brand-mark"></span>MERIDIAN SYSTEMS</div>
      <p class="brand-links">Privacy<span class="dot">•</span>Remote Support<span class="dot">•</span>Contact Us</p>
      <p class="copyright">Copyright 2007-2024 Meridian Systems</p>
    </div>
    <div class="form-pane">
      <h1 class="title">Login to MRDS</h1>
      <div class="db-row"><svg class="back" style="color:#888"><use href="#i-back"/></svg><span class="divider"></span><svg class="db-icon"><use href="#i-db"/></svg>Database : ABC12345</div>
      <div class="field" style="top:135px"><svg style="color:#666"><use href="#i-user"/></svg><span class="value">JohnDoe123</span><svg class="tool"><use href="#i-clear"/></svg></div>
      <div class="field is-focus" style="top:167px"><svg style="color:#666"><use href="#i-lock"/></svg><span class="value dots">●●●|</span><svg class="tool"><use href="#i-eye"/></svg><span class="sep"></span><svg class="tool"><use href="#i-clear"/></svg></div>
      <a class="forgot">Forgot Password?</a>
      <div class="btn" style="left:287px;top:211px;width:53px">LOGIN</div>
      <div class="or-rule"><span>OR</span></div>
      <div class="sso" style="left:107px"><div class="mark"></div>Login with<br>Keyway</div>
      <div class="sso" style="left:187px"><div class="mark"></div>Login with<br>Northgate</div>
      <div class="sso" style="left:267px"><div class="mark"></div>Login with<br>SinglePass</div>
      <p class="notice">All activity on this site is being recorded. Your IP Address is being saved as '<b>192.168.168.134</b>'.</p>
    </div>
  </section>

  <!-- Step 2: error -->
  <section class="screen" style="left:1733px;top:541px">
    <div class="brand-pane">
      <div class="brand-name"><span class="brand-mark"></span>MERIDIAN SYSTEMS</div>
      <p class="brand-links">Privacy<span class="dot">•</span>Remote Support<span class="dot">•</span>Contact Us</p>
      <p class="copyright">Copyright 2007-2024 Meridian Systems</p>
    </div>
    <div class="form-pane">
      <div class="alert">Invalid username and/or password. Please enter the correct data and try again.</div>
      <h1 class="title">Login to MRDS</h1>
      <div class="db-row"><svg class="back" style="color:#888"><use href="#i-back"/></svg><span class="divider"></span><svg class="db-icon"><use href="#i-db"/></svg>Database : ABC12345</div>
      <div class="field is-error" style="top:135px"><svg style="color:#666"><use href="#i-user"/></svg><span class="value">johndoe</span><svg class="tool"><use href="#i-clear"/></svg></div>
      <div class="field is-error" style="top:167px"><svg style="color:#666"><use href="#i-lock"/></svg><span class="value dots">●●●●●●</span><svg class="tool"><use href="#i-eye"/></svg><span class="sep"></span><svg class="tool"><use href="#i-clear"/></svg></div>
      <a class="forgot">Forgot Password?</a>
      <div class="btn" style="left:287px;top:211px;width:53px">LOGIN</div>
      <div class="or-rule"><span>OR</span></div>
      <div class="sso" style="left:107px"><div class="mark"></div>Login with<br>Keyway</div>
      <div class="sso" style="left:187px"><div class="mark"></div>Login with<br>Northgate</div>
      <div class="sso" style="left:267px"><div class="mark"></div>Login with<br>SinglePass</div>
      <p class="notice">All activity on this site is being recorded. Your IP Address is being saved as '<b>192.168.168.134</b>'.</p>
    </div>
  </section>

</main>
</body>
</html>
```